Locksmith Business Cards

My father-in-law is in need of new business cards for his locksmith business and I need to impress him. Kindly help me out!

You can see the previous business card attached. It is a family run business in North Wales.

No individual names on the cards.

Key Things to Feature:
- The words "Prompt", "Local", "Reliable" (as you can see under the logo on the website)
- 24h Emergency Service
- Covering All of North Wales, the Wirral and Chester
- The color blue
- A key or a lock would be interesting (similar to the ones that come up when you google locksmith business card)

Optional (only if design includes bullet points, like the example below):
https://imgvaultcdn.net/samples/208314/55172/55172_3904821_208314_image.jpg
- Residential / Commercial / Automotive
- Alarms & Cameras
- Key Cutting & Safes

https://www.brynhafod-locksmiths.co.uk/

Industry/Entity Type

Locksmith

Contact Information for Business Card

01632 960 418
07700 900 362
brynhafodlocksmiths@mailvane.com
Brynhafod Locksmiths, The Willow Barn, 7 Tannery Rd., Llandudno LL99 4QX
www.brynhafod-locksmiths.co.uk

Requirements
Must have
• - The words "Prompt", "Local", "Reliable" (as you can see under the logo on the website)
• - 24h Emergency Service
• - Covering All of North Wales, the Wirral and Chester
Nice to have
• - A key or a lock would be interesting (similar to the ones that come up when you google locksmith business card)

```html
<!DOCTYPE html>
<html lang="en">
<head>
<meta charset="utf-8">
<title>Brynhafod Locksmiths – Business Card</title>
<link rel="stylesheet" href="https://fonts.googleapis.com/css2?family=Roboto+Condensed:wght@500&family=Roboto:wght@400&display=swap">
<style>
  :root {
    --stage: #3b3b3d;
    --navy: #1f2467;
    --navy-deep: #191d58;
    --periwinkle: #6e82c4;
    --stripe: #4a5aa8;
    --paper: #ffffff;
    --ink: #2b2b33;
    --white: #ffffff;
  }
  * { box-sizing: border-box; margin: 0; padding: 0; }
  html, body {
    width: 1200px; height: 900px; overflow: hidden;
    background: var(--stage);
  }
  .stage {
    position: relative; width: 1200px; height: 900px;
    display: flex; flex-direction: column; align-items: center;
    justify-content: center; gap: 42px;
  }
  .card {
    position: relative; width: 680px; height: 388px; overflow: hidden;
    border-radius: 2px; box-shadow: 0 10px 30px rgba(0,0,0,.45);
  }

  /* Front */
  .card--front {
    background: linear-gradient(215deg, var(--periwinkle) 0%, #3d4796 45%, var(--navy-deep) 100%);
    color: var(--white);
    font-family: "Roboto", Arial, sans-serif;
  }
  .front-brand {
    position: absolute; left: 0; right: 0; top: 96px;
    display: flex; justify-content: center; align-items: center; gap: 18px;
  }
  .brand-mark {
    width: 62px; height: 62px; border-radius: 10px; background: var(--white);
    flex: none;
  }
  .brand-name {
    font-family: "Roboto Condensed", "Arial Narrow", sans-serif;
    font-weight: 500; font-size: 40px; line-height: 40px; letter-spacing: .5px;
    text-transform: uppercase;
  }
  .front-tagline {
    position: absolute; left: 0; right: 0; top: 232px;
    text-align: center; font-size: 15.5px; line-height: 20px; letter-spacing: .3px;
  }
  .front-tagline .values { letter-spacing: 1px; }

  /* Back */
  .card--back {
    background: var(--paper); color: var(--ink);
    font-family: "Roboto", Arial, sans-serif;
  }
  .back-wave { position: absolute; inset: 0; width: 680px; height: 388px; }
  .back-brand {
    position: absolute; left: 78px; top: 42px;
    display: flex; align-items: center; gap: 12px; color: var(--navy);
  }
  .back-brand .brand-mark { width: 52px; height: 52px; background: var(--navy); border-radius: 8px; }
  .back-brand .brand-name { font-size: 34px; line-height: 33px; }
  .services {
    position: absolute; left: 40px; top: 138px; width: 320px;
    text-align: center; font-size: 15.5px; line-height: 19px; color: var(--ink);
  }
  .contact {
    position: absolute; left: 368px; top: 124px; list-style: none;
    font-size: 16px; line-height: 25px; color: var(--ink);
  }
  .contact li { display: flex; align-items: center; gap: 9px; white-space: nowrap; }
  .contact svg { width: 16px; height: 16px; fill: var(--stripe); flex: none; }
  .address {
    position: absolute; left: 392px; top: 306px;
    display: flex; gap: 10px; color: var(--white); font-size: 18px; line-height: 27px;
  }
  .address svg { width: 16px; height: 20px; fill: var(--white); margin-top: 3px; flex: none; }
</style>
</head>
<body>
<main class="stage">

  <section class="card card--front" aria-label="Card front">
    <div class="front-brand">
      <span class="brand-mark"></span>
      <div class="brand-name">Brynhafod<br>Locksmiths</div>
    </div>
    <p class="front-tagline">
      <span class="values">PROMPT - LOCAL - RELIABLE</span><br>
      24h Emergency Service<br>
      Covering All of North Wales, the Wirral and Chester
    </p>
  </section>

  <section class="card card--back" aria-label="Card back">
    <svg class="back-wave" viewBox="0 0 680 388" aria-hidden="true">
      <path d="M0,230 C70,262 160,305 262,322 C160,314 70,282 0,254 Z" fill="var(--stripe)"/>
      <path d="M0,272 C80,304 150,328 230,330 C330,320 500,250 680,230 L680,388 L0,388 Z" fill="var(--navy)"/>
    </svg>

    <div class="back-brand">
      <span class="brand-mark"></span>
      <div class="brand-name">Brynhafod<br>Locksmiths</div>
    </div>

    <p class="services">
      Residential | Commercial | Automotive<br>
      Alarms &amp; Cameras<br>
      Key Cutting &amp; Safes
    </p>

    <ul class="contact">
      <li><svg viewBox="0 0 24 24"><path d="M6.6 10.8a15 15 0 0 0 6.6 6.6l2.2-2.2c.3-.3.7-.4 1-.2 1.1.4 2.3.6 3.6.6.6 0 1 .4 1 1V20c0 .6-.4 1-1 1A17 17 0 0 1 3 4c0-.6.4-1 1-1h3.5c.6 0 1 .4 1 1 0 1.3.2 2.5.6 3.6.1.3 0 .7-.2 1z"/></svg>01632 960 418</li>
      <li><svg viewBox="0 0 24 24"><path d="M6.6 10.8a15 15 0 0 0 6.6 6.6l2.2-2.2c.3-.3.7-.4 1-.2 1.1.4 2.3.6 3.6.6.6 0 1 .4 1 1V20c0 .6-.4 1-1 1A17 17 0 0 1 3 4c0-.6.4-1 1-1h3.5c.6 0 1 .4 1 1 0 1.3.2 2.5.6 3.6.1.3 0 .7-.2 1z"/></svg>07700 900 362</li>
      <li><svg viewBox="0 0 24 24"><path d="M2 5h20v14H2z"/><path d="M3 6.5l9 7 9-7" fill="none" stroke="#fff" stroke-width="1.6"/></svg>brynhafodlocksmiths@mailvane.com</li>
      <li><svg viewBox="0 0 24 24"><circle cx="12" cy="12" r="10"/><path d="M2 12h20M12 2c3 3 3 17 0 20M12 2c-3 3-3 17 0 20" fill="none" stroke="#fff" stroke-width="1.4"/></svg>www.brynhafod-locksmiths.co.uk</li>
    </ul>

    <div class="address">
      <svg viewBox="0 0 16 20"><path d="M8 0a7 7 0 0 0-7 7c0 5 7 13 7 13s7-8 7-13a7 7 0 0 0-7-7zm0 10a3 3 0 1 1 0-6 3 3 0 0 1 0 6z"/></svg>
      <p>The Willow Barn, 7 Tannery Rd.<br>Llandudno LL99 4QX</p>
    </div>
  </section>

</main>
</body>
</html>
```